Social Media App Needs PPT Template

We need a PowerPoint template for a new social media company based in the DC area called "Bold Ledger." We provide an interactive digital platform for executives to share actionable advice. We would like to see designs that use our orange logo color as an accent, but are mainly grey, white, and black. The final design should communicate clean, chic, modern, and professional.

Target Market(s)

Executives

Industry/Entity Type

Information Technology

Font styles to use
Sans Serif

Colors
f78f20
fbe7d2
ffffff
000000
e8e8e8
757575

Requirements
Must have
• My project must have title page and many options for the body of the ppt (graphs, tables, etc). It also needs to be easy to modify. I must have someone who is experienced in creating powerpoint templates.
Nice to have
• It would be nice to have a very modern and clean design that includes the logo on every page, but still leaves a lot of room for the content of the slide
Should not have
• My design project should not look to busy.

```html
<!DOCTYPE html>
<html lang="en">
<head>
<meta charset="utf-8">
<title>Bold Ledger – About Our Company</title>
<link href="https://fonts.googleapis.com/css2?family=Lato:wght@300;400;700&display=swap" rel="stylesheet">
<style>
  :root {
    --stage: #555555;
    --slide-bg: #f4f4f4;
    --orange: #f0921e;
    --orange-deep: #e8801a;
    --navy: #232d3b;
    --grey-bar: #6d6e70;
    --text: #555555;
    --axis: #8a8a8a;
    --white: #ffffff;
  }
  * { margin: 0; padding: 0; box-sizing: border-box; }
  html, body { width: 1200px; height: 960px; overflow: hidden; }
  body { background: var(--stage); font-family: "Lato", sans-serif; position: relative; }

  .slide {
    position: absolute; left: 111px; top: 135px;
    width: 970px; height: 727px;
    background: radial-gradient(ellipse at 50% 40%, #ffffff 0%, var(--slide-bg) 70%);
    overflow: hidden;
  }
  .slide-frame { position: absolute; inset: 0; width: 970px; height: 727px; }

  .slide-title {
    position: absolute; left: 30px; top: 60px;
    font-weight: 300; font-size: 37px; color: var(--white); letter-spacing: 0.2px;
  }
  .brand {
    position: absolute; left: 700px; top: 67px;
    display: flex; align-items: center; gap: 9px;
    font-weight: 700; font-size: 22px; color: var(--white);
  }
  .brand-dot { width: 18px; height: 18px; border-radius: 50%; background: var(--orange); }

  .chart { position: absolute; left: 0; top: 0; width: 970px; height: 520px; }
  .chart text { font-family: "Lato", sans-serif; fill: var(--text); }

  .body-copy {
    position: absolute; left: 50px; top: 529px; width: 879px;
    font-size: 17px; line-height: 24.8px; color: var(--text); text-align: justify;
  }
  .footer-text {
    position: absolute; left: 26px; top: 694px;
    font-size: 13px; color: #d7d9dc;
  }
  .footer-text .sep { margin: 0 7px; }
</style>
</head>
<body>
  <section class="slide">
    <svg class="slide-frame" viewBox="0 0 970 727" aria-hidden="true">
      <!-- header -->
      <polygon points="753,33 970,33 970,42 744,42" fill="var(--orange)"/>
      <polygon points="0,46 737,46 657,122 0,122" fill="var(--orange-deep)"/>
      <polygon points="560,46 737,46 697,84 520,84" fill="var(--orange)" opacity="0.55"/>
      <polygon points="668,46 970,46 970,122 588,122" fill="var(--white)"/>
      <polygon points="673,46 970,46 970,122 593,122" fill="var(--orange-deep)" opacity="0"/>
      <polygon points="746,46 970,46 970,122 665,122" fill="var(--navy)"/>
      <polygon points="0,125 653,125 643,135 0,135" fill="var(--navy)"/>
      <!-- footer -->
      <polygon points="0,689 277,689 249,717 0,717" fill="var(--navy)"/>
      <polygon points="281,689 970,689 970,717 253,717" fill="var(--orange-deep)"/>
    </svg>

    <h1 class="slide-title">About Our Company</h1>
    <div class="brand"><span class="brand-dot"></span>Bold Ledger</div>

    <svg class="chart" viewBox="0 0 970 520" role="img" aria-label="Bar chart of three series across three categories">
      <g stroke="var(--axis)" stroke-width="1" stroke-dasharray="8 6" opacity="0.8">
        <line x1="80" y1="212" x2="802" y2="212"/>
        <line x1="80" y1="261" x2="802" y2="261"/>
        <line x1="80" y1="310" x2="802" y2="310"/>
        <line x1="80" y1="358" x2="802" y2="358"/>
        <line x1="80" y1="407" x2="802" y2="407"/>
      </g>
      <g>
        <rect x="119.2" y="246.2" width="47.2" height="209.8" fill="var(--orange)"/>
        <rect x="166.4" y="287.7" width="47.2" height="168.3" fill="var(--navy)"/>
        <rect x="213.6" y="263.3" width="47.2" height="192.7" fill="var(--grey-bar)"/>
        <rect x="342.4" y="275.4" width="47.2" height="180.6" fill="var(--orange)"/>
        <rect x="389.6" y="243.7" width="47.2" height="212.3" fill="var(--navy)"/>
        <rect x="436.8" y="290.1" width="47.2" height="165.9" fill="var(--grey-bar)"/>
        <rect x="557.6" y="302.3" width="47.2" height="153.7" fill="var(--orange)"/>
        <rect x="604.8" y="256.0" width="47.2" height="200.0" fill="var(--navy)"/>
        <rect x="652.0" y="238.8" width="47.2" height="217.2" fill="var(--grey-bar)"/>
      </g>
      <g stroke="var(--axis)" stroke-width="1">
        <line x1="79" y1="212" x2="79" y2="458"/>
        <line x1="74" y1="456" x2="802" y2="456"/>
      </g>
      <g font-size="16" text-anchor="end">
        <text x="62" y="217">5</text>
        <text x="62" y="266">4</text>
        <text x="62" y="315">3</text>
        <text x="62" y="363">2</text>
        <text x="62" y="412">1</text>
        <text x="62" y="461">0</text>
      </g>
      <g font-size="17" text-anchor="middle">
        <text x="186.4" y="489">Category 1</text>
        <text x="408.8" y="489">Category 2</text>
        <text x="632.8" y="489">Category 3</text>
      </g>
      <g font-size="19">
        <rect x="849" y="206" width="10" height="10" fill="var(--orange)"/>
        <text x="864" y="219">Series 1</text>
        <rect x="849" y="231" width="10" height="10" fill="var(--navy)"/>
        <text x="864" y="244">Series 2</text>
        <rect x="849" y="257" width="10" height="10" fill="var(--grey-bar)"/>
        <text x="864" y="270">Series 3</text>
      </g>
    </svg>

    <p class="body-copy">Duis autem vel eum iriure dolor in hendrerit in vulputate velit esse molestie consequat, vel illum dolore eu feugiat nulla facilisis at vero eros et accumsan et iusto odio dignissim qui blandit praesent luptatum zzril delenit augue duis dolore te feugait nulla facilisi. Nam liber tempor cum soluta nobis eleifend option congue nihil imperdiet doming id quod mazim placerat facer possim assum.</p>

    <div class="footer-text">www.boldledger.com<span class="sep">|</span>Page 4</div>
  </section>
</body>
</html>
```